*** Business Card Design Project

As a starting point, please take a look at our website www.plurvanta.com as a starting point.

We are looking for you to design our new business cards for plurvanta, something funky, cool and potentially unusual/different.

Good luck.

Industry/Entity Type

Business

```html
<!DOCTYPE html>
<html lang="en">
<head>
<meta charset="utf-8">
<title>plurvanta business cards</title>
<link rel="stylesheet" href="https://fonts.googleapis.com/css2?family=Open+Sans:wght@400;600;700&display=swap">
<style>
  :root {
    --page: #e4e4e2;
    --orange: #ee5a0c;
    --orange-deep: #e04a06;
    --orange-light: #f7861f;
    --card-white: #fbfbfa;
    --ink: #4a4a4a;
    --white: #ffffff;
  }
  * { margin: 0; padding: 0; box-sizing: border-box; }
  html, body { width: 1200px; height: 1200px; overflow: hidden; }
  body {
    background: var(--page);
    font-family: "Open Sans", sans-serif;
    display: flex;
    flex-direction: column;
    align-items: center;
    justify-content: center;
    gap: 60px;
  }
  .card {
    position: relative;
    width: 860px;
    height: 491px;
    overflow: hidden;
    box-shadow: 0 4px 14px rgba(0,0,0,0.12);
  }
  .card--front {
    background: radial-gradient(ellipse at 40% 30%, var(--orange-light) 0%, var(--orange) 45%, var(--orange-deep) 100%);
    color: var(--white);
  }
  .card--back { background: var(--card-white); color: var(--ink); }

  .brand { position: absolute; left: 56px; }
  .brand__name {
    font-weight: 600;
    font-size: 66px;
    line-height: 1.15;
    letter-spacing: -1px;
  }
  .brand__tagline {
    font-size: 19px;
    font-weight: 400;
    margin-top: 6px;
  }
  .card--front .brand { top: 96px; }
  .card--back .brand { top: 36px; color: var(--orange); }

  .contact-list {
    position: absolute;
    left: 56px;
    top: 240px;
    list-style: none;
    font-size: 16px;
  }
  .contact-list li {
    display: flex;
    align-items: center;
    gap: 12px;
    margin-bottom: 14px;
  }
  .contact-list svg { width: 22px; height: 22px; flex: none; }

  .details {
    position: absolute;
    left: 56px;
    top: 176px;
    list-style: none;
    font-size: 21px;
    line-height: 1.45;
  }
  .details__label { color: var(--orange); font-weight: 700; }

  .word-cloud {
    position: absolute;
    right: 30px;
    top: 60px;
    width: 190px;
    height: 390px;
  }
</style>
</head>
<body>

<section class="card card--front" aria-label="Card front">
  <div class="brand">
    <div class="brand__name">plurvanta</div>
    <div class="brand__tagline">The digital specialist recruitment company.</div>
  </div>
  <ul class="contact-list">
    <li>
      <svg viewBox="0 0 22 22"><circle cx="11" cy="11" r="10" fill="none" stroke="#fff" stroke-width="1.5"/><path d="M7.5 6.5c0 5 3 8 8 8l1-2-2.2-1-1 1c-1.5-.6-2.7-1.8-3.3-3.3l1-1-1-2.2z" fill="#fff"/></svg>
      +44 203 418 2270
    </li>
    <li>
      <svg viewBox="0 0 22 22"><circle cx="11" cy="11" r="10" fill="none" stroke="#fff" stroke-width="1.5"/><path d="M11 5a4 4 0 0 0-4 4c0 3 4 8 4 8s4-5 4-8a4 4 0 0 0-4-4zm0 5.5a1.5 1.5 0 1 1 0-3 1.5 1.5 0 0 1 0 3z" fill="#fff"/></svg>
      14 - 16 Larkmoor Lane London EC2R 7TN
    </li>
    <li>
      <svg viewBox="0 0 22 22"><circle cx="11" cy="11" r="10" fill="none" stroke="#fff" stroke-width="1.5"/><rect x="6" y="7.5" width="10" height="7" fill="none" stroke="#fff" stroke-width="1.3"/><path d="M6 7.5l5 4 5-4" fill="none" stroke="#fff" stroke-width="1.3"/></svg>
      info@plurvanta.com
    </li>
  </ul>
  <svg class="word-cloud" viewBox="0 0 190 390" role="img" aria-label="Decorative word cloud of digital terms such as cloud, mobile, VOIP and jobs">
    <defs>
      <radialGradient id="cloud-front" cx="0.5" cy="0.5" r="0.6">
        <stop offset="0" stop-color="#fff" stop-opacity="0.35"/>
        <stop offset="1" stop-color="#fff" stop-opacity="0"/>
      </radialGradient>
    </defs>
    <rect width="190" height="390" fill="url(#cloud-front)"/>
  </svg>
</section>

<section class="card card--back" aria-label="Card back">
  <div class="brand">
    <div class="brand__name">plurvanta</div>
    <div class="brand__tagline">The digital specialist recruitment company.</div>
  </div>
  <ul class="details">
    <li><span class="details__label">Name:</span> Maren Holt</li>
    <li><span class="details__label">Job Title:</span> Sales Manager</li>
    <li><span class="details__label">Direct Line:</span> 0845 310 5527</li>
    <li><span class="details__label">Mobile Number:</span> 079 612 884 20</li>
    <li><span class="details__label">Chat:</span> mholt84</li>
    <li><span class="details__label">Email:</span> maren.holt@plurvanta.com</li>
    <li><span class="details__label">Address:</span> 2260 Linden Ave, Fairbrook, OH, United States.</li>
  </ul>
  <svg class="word-cloud" viewBox="0 0 190 390" role="img" aria-label="Decorative word cloud of digital terms such as cloud, mobile, VOIP and jobs">
    <defs>
      <radialGradient id="cloud-back" cx="0.5" cy="0.5" r="0.6">
        <stop offset="0" stop-color="#f47a1a" stop-opacity="0.4"/>
        <stop offset="1" stop-color="#f47a1a" stop-opacity="0"/>
      </radialGradient>
    </defs>
    <rect width="190" height="390" fill="url(#cloud-back)"/>
  </svg>
</section>

</body>
</html>
```